Professional and creative business card design for recruiting service providers

Our company supports German medium-sized companies in filling vacancies promptly. For this we use social media marketing and bring our customers into the visibility.

We want a professional but also creative design for our business cards.

Please look at lindqvar-staff.de to get an impression of our CI.

Target Market(s)

Small and medium-sized companies in Germany from the industry

Industry/Entity Type

Industrie, Handwerk

Contact Information for Business Card

Name, Position, Telefonnummer, Email, Website

Colors
EE7325
F08F49
F5BC92
FAE3D3
FDF4ED

Requirements
Must have
• A picture of the employee and in the style of www.lindqvar-staff.de

```html
<!DOCTYPE html>
<html lang="en">
<head>
<meta charset="utf-8">
<title>Lindqvar &amp; Staff – Business Card</title>
<link rel="stylesheet" href="https://fonts.googleapis.com/css2?family=Montserrat:wght@700;800&family=Arimo:wght@400;700&display=swap">
<style>
  :root {
    --stage: #2b2b2d;
    --card: #121213;
    --orange: #ee7325;
    --orange-soft: #f08f49;
    --white: #ffffff;
    --photo-top: #1c1c1f;
    --photo-bottom: #2e2f3a;
  }
  * { box-sizing: border-box; margin: 0; padding: 0; }
  html, body {
    width: 1200px; height: 1015px; overflow: hidden;
    background: var(--stage);
  }
  .stage {
    width: 1200px; height: 1015px;
    display: flex; flex-direction: column; align-items: center; justify-content: center;
    gap: 40px;
  }
  .card {
    position: relative;
    width: 820px; height: 450px;
    background: var(--card);
    overflow: hidden;
    box-shadow: 0 10px 30px rgba(0,0,0,.45);
  }
  .card__strip {
    position: absolute; left: 0; right: 0; bottom: 0;
    height: 9px; background: var(--orange);
  }
  .wordmark {
    font-family: "Montserrat", sans-serif;
    font-weight: 800;
    color: var(--white);
    letter-spacing: .14em;
    text-transform: uppercase;
    line-height: 1.05;
  }

  /* back */
  .card--back .wordmark {
    position: absolute; left: 70px; bottom: 70px;
    font-size: 44px;
  }
  .card--back .wordmark span { display: block; }
  .card--back .wordmark span + span { padding-left: 30px; }

  /* front */
  .brand {
    position: absolute; left: 54px; top: 92px;
    display: flex; align-items: center; gap: 22px;
  }
  .brand__square {
    width: 74px; height: 74px; background: var(--orange);
  }
  .brand .wordmark { font-size: 34px; }
  .brand .wordmark span { display: block; }
  .brand .wordmark span + span { padding-left: 18px; }

  .person {
    position: absolute; left: 70px; top: 232px;
  }
  .person__name {
    font-family: "Montserrat", sans-serif;
    font-weight: 800; font-size: 30px;
    color: var(--orange); letter-spacing: .05em;
    text-transform: uppercase;
  }
  .person__role {
    font-family: "Arimo", sans-serif;
    font-size: 25px; color: var(--white);
    margin-top: 2px;
  }
  .contacts {
    position: absolute; left: 78px; top: 330px;
    list-style: none;
    font-family: "Arimo", sans-serif;
    font-size: 24px; color: var(--white);
    letter-spacing: .03em;
  }
  .contacts li { display: flex; align-items: center; gap: 14px; height: 34px; }
  .contacts svg { width: 24px; height: 24px; flex: none; }
  .contacts .accent { color: var(--orange); }

  .portrait {
    position: absolute; right: 0; bottom: 9px;
    width: 360px; height: 400px;
    background: linear-gradient(180deg, var(--photo-top) 0%, var(--photo-bottom) 100%);
    clip-path: polygon(28% 0, 72% 0, 74% 30%, 100% 42%, 100% 100%, 0 100%, 0 45%, 26% 30%);
  }
</style>
</head>
<body>
<main class="stage">

  <section class="card card--back" aria-label="Card back">
    <h1 class="wordmark"><span>Lindqvar</span><span>&amp; Staff</span></h1>
    <div class="card__strip"></div>
  </section>

  <section class="card card--front" aria-label="Card front">
    <div class="brand">
      <div class="brand__square"></div>
      <p class="wordmark"><span>Lindqvar</span><span>&amp; Staff</span></p>
    </div>

    <div class="person">
      <h2 class="person__name">Jonas Hartwig</h2>
      <p class="person__role">Managing Director</p>
    </div>

    <ul class="contacts">
      <li>
        <svg viewBox="0 0 24 24" fill="var(--orange)"><path d="M6.6 10.8a15.1 15.1 0 0 0 6.6 6.6l2.2-2.2a1 1 0 0 1 1-.25 11.4 11.4 0 0 0 3.6.57 1 1 0 0 1 1 1V20a1 1 0 0 1-1 1A17 17 0 0 1 3 4a1 1 0 0 1 1-1h3.5a1 1 0 0 1 1 1c0 1.25.2 2.45.57 3.6a1 1 0 0 1-.25 1z"/></svg>
        040-318 752 946
      </li>
      <li>
        <svg viewBox="0 0 24 24" fill="none" stroke="var(--orange)" stroke-width="2"><rect x="2" y="5" width="20" height="14"/><path d="M2 5l10 8 10-8"/></svg>
        info@lindqvar-staff.de
      </li>
      <li>
        <svg viewBox="0 0 24 24" fill="none" stroke="var(--orange)" stroke-width="1.8"><circle cx="12" cy="12" r="10"/><path d="M2 12h20M12 2c3 3 3 17 0 20M12 2c-3 3-3 17 0 20"/></svg>
        <span>www.<span class="accent">lindqvar-staff</span>.de</span>
      </li>
    </ul>

    <div class="portrait" role="img" aria-label="Portrait photo of the employee in a dark blazer and turtleneck"></div>
    <div class="card__strip"></div>
  </section>

</main>
</body>
</html>
```